Orvane Mechanical - Letterhead

We are a plumbing and hvac company based in Calgary. This letterhead will be on our quotes, invoices, preventative maintenance proposals etc.

```html
<!DOCTYPE html>
<html lang="en">
<head>
<meta charset="utf-8">
<title>Orvane Mechanical – Letterhead</title>
<link rel="stylesheet" href="https://fonts.googleapis.com/css2?family=Figtree:ital,wght@0,400;0,600;0,800;1,600;1,700&family=Work+Sans:wght@400&display=swap">
<style>
  :root{
    --orange:#ef5a24;
    --blue:#2272bb;
    --ink:#4a4a4a;
    --body:#6e6e6e;
    --paper:#ffffff;
    --backdrop:#e9e7e4;
  }
  *{margin:0;padding:0;box-sizing:border-box}
  html,body{width:1185px;height:1200px;overflow:hidden;background:var(--backdrop)}
  .letterhead{
    position:absolute;left:182px;top:20px;width:820px;height:1160px;
    background:var(--paper);box-shadow:0 2px 10px rgba(0,0,0,.18);
    font-family:"Figtree",sans-serif;color:var(--body);overflow:hidden;
  }
  .brand{position:absolute;left:76px;top:112px;display:flex;align-items:center;gap:10px}
  .brand-dot{width:14px;height:14px;border-radius:50%;background:var(--orange)}
  .brand-name{font-weight:800;color:var(--blue);font-size:24px;line-height:1.05;letter-spacing:.5px;text-transform:uppercase}
  .contact{position:absolute;top:125px;font-family:"Work Sans",sans-serif;font-size:13px;line-height:16.5px;color:#333}
  .contact-lines{left:381px}
  .contact-lines li{list-style:none;display:flex;align-items:center;gap:6px}
  .contact-lines svg{width:9px;height:9px;flex:none}
  .contact-address{left:605px;top:141.5px;font-style:normal}
  .header-rule{position:absolute;left:76px;top:198px;width:670px;height:1.5px;background:var(--orange)}
  .salutation{position:absolute;left:76px;top:284px;font-size:23px;font-weight:600;color:var(--ink)}
  .body-copy{position:absolute;left:76px;width:670px;font-size:12.6px;line-height:21px;text-align:justify;text-align-last:justify}
  .p1{top:338px}.p2{top:451px}.p3{top:541px}.p4{top:777px}
  .signer{position:absolute;left:76px;top:846px;color:var(--ink);font-style:italic}
  .signer-name{font-size:23px;font-weight:700;line-height:26px}
  .signer-role{font-size:12.5px;font-weight:600;line-height:14px}
  .signature{position:absolute;left:76px;top:916px;width:214px;height:70px;background:linear-gradient(90deg,#f1f1f1,#e4e4e4);border-radius:4px}
  .footer-band{position:absolute;left:0;bottom:0;width:820px}
  .footer-stripe{bottom:30px;height:6px;background:var(--orange)}
  .footer-base{height:30px;background:var(--blue)}
</style>
</head>
<body>
<main class="letterhead">
  <div class="brand">
    <span class="brand-dot"></span>
    <div class="brand-name">Orvane<br>Mechanical</div>
  </div>

  <ul class="contact contact-lines">
    <li><svg viewBox="0 0 10 10"><path d="M2 1l2 2-1 1.2c.6 1.3 1.5 2.2 2.8 2.8L7 6l2 2-1.2 1.5C4.5 9.3.7 5.5.5 2.2z" fill="var(--blue)"/></svg>(403) 555-0186</li>
    <li><svg viewBox="0 0 10 10"><rect x=".8" y="2" width="8.4" height="6" fill="none" stroke="var(--blue)" stroke-width="1"/><path d="M1 2.3l4 3 4-3" fill="none" stroke="var(--blue)" stroke-width="1"/></svg>info@orvanemech.com</li>
    <li><svg viewBox="0 0 10 10"><circle cx="5" cy="5" r="4.2" fill="none" stroke="var(--blue)" stroke-width=".9"/><path d="M.8 5h8.4M5 .8c-2 2.5-2 5.9 0 8.4M5 .8c2 2.5 2 5.9 0 8.4" fill="none" stroke="var(--blue)" stroke-width=".7"/></svg>www.orvanemech.com</li>
  </ul>
  <address class="contact contact-address">2140 Kestrel Road NE<br>Calgary, AB T2E 4K1</address>

  <div class="header-rule"></div>

  <h1 class="salutation">Dear sir/Madam,</h1>

  <p class="body-copy p1">Lorem ipsum dolor sit amet, consectetur adipiscing elit. Sed do eiusmod tempor incididunt ut labore et dolore magna aliqua. Ut enim ad minim veniam, quis nostrud exercitation ullamco laboris nisi ut aliquip ex ea commodo consequat. Duis aute irure dolor in reprehenderit in voluptate velit esse cillum dolore eu fugiat nulla pariatur. Excepteur sint occaecat cupidatat non proident, sunt in culpa qui officia</p>
  <p class="body-copy p2">deserunt mollit anim id est laborum. Curabitur pretium tincidunt lacus, nulla gravida orci a odio. Nullam varius, turpis et commodo pharetra, est eros bibendum elit, nec luctus magna felis sollicitudin mauris. Integer in mauris eu nibh euismod gravida. Duis ac tellus et risus vulputate vehicula. Donec lobortis</p>
  <p class="body-copy p3">Praesent sapien massa, convallis a pellentesque nec, egestas non nisi. Vivamus magna justo, lacinia eget consectetur sed, convallis at tellus. Mauris blandit aliquet elit, eget tincidunt nibh pulvinar a. Nulla porttitor accumsan tincidunt. Cras ultricies ligula sed magna dictum porta. Vestibulum ante ipsum primis in faucibus orci luctus et ultrices posuere cubilia curae; donec velit neque, auctor sit amet aliquam vel, ullamcorper sit amet ligula. Proin eget tortor risus. Pellentesque in ipsum id orci porta dapibus. Quisque velit nisi, pretium ut lacinia in, elementum id enim. Sed porttitor lectus nibh. Curabitur arcu erat, accumsan id imperdiet et, porttitor at sem. Nulla quis lorem ut libero malesuada feugiat. Vivamus suscipit tortor eget felis porttitor volutpat. Aliquam erat volutpat, nunc fermentum tortor ac porta dapibus, tellus nisl consequat lorem, vitae ultricies mi arcu sed augue. Etiam rhoncus maecenas tempus, tellus eget condimentum rhoncus, sem quam semper libero, sit amet adipiscing sem neque sed ipsum. Nam quam nunc, blandit vel</p>
  <p class="body-copy p4">luctus pulvinar, hendrerit id lorem. Maecenas nec odio et ante tincidunt tempus. Donec vitae sapien ut libero venenatis faucibus. Nullam quis ante, etiam sit amet orci eget eros faucibus tincidunt duis leo sed</p>

  <div class="signer">
    <div class="signer-name">Daniel Korsby</div>
    <div class="signer-role">Director</div>
  </div>
  <div class="signature" role="img" aria-label="Director's handwritten signature"></div>

  <div class="footer-band footer-stripe"></div>
  <div class="footer-band footer-base"></div>
</main>
</body>
</html>
```